Business Card Design

We are looking for a business card designed for our landscaping company. We do landscaping installation & Maintenance Services. We would like to see designs that have basic landscaping in background. We also think it is important to have both of our names and phone numbers on the card. We need something that stands out a little whether it is shape of the card or thickness or design.

Business

Bramblewood Yardworks, bramblewoodyard@mailvista.net, Owen Platt 555-273-9104, Daniel Korbin 555-618-3927

```html
<!DOCTYPE html>
<html lang="en">
<head>
<meta charset="UTF-8">
<title>Bramblewood Yardworks — Business Card</title>
<link href="https://fonts.googleapis.com/css2?family=Bodoni+Moda:opsz,wght@6..96,500;6..96,600&family=Open+Sans:wght@400&display=swap" rel="stylesheet">
<style>
  :root {
    --page-bg: #d9d6d1;
    --frost-top: #f4f6f8;
    --frost-bottom: #dfe4e8;
    --ink: #1b1b1b;
    --leaf: #2f9a45;
    --leaf-light: #4cb05c;
    --cream: #e8dfcf;
    --night: #0d0d0f;
    --night-soft: #2a2a2d;
    --rose-1: #c79a94;
    --rose-2: #f0d6d0;
    --rose-3: #9d6e6a;
    --gold-1: #a88c63;
    --gold-2: #ecdcb8;
    --gold-3: #7f6744;
  }
  * { margin: 0; padding: 0; box-sizing: border-box; }
  html, body {
    width: 1200px; height: 970px; overflow: hidden;
    background: var(--page-bg);
  }
  .card {
    position: absolute;
    left: 100px; top: 186px;
    width: 1000px; height: 598px;
    background: linear-gradient(170deg, var(--frost-top), var(--frost-bottom));
    box-shadow: 0 14px 40px rgba(0,0,0,.25);
    overflow: hidden;
  }
  .card-waves { position: absolute; inset: 0; width: 1000px; height: 598px; }
  .company-name {
    position: absolute; left: 0; right: 0; top: 100px;
    text-align: center;
    font-family: "Bodoni Moda", "Didot", serif;
    font-weight: 600; font-size: 60px; letter-spacing: -0.5px;
    color: var(--ink);
  }
  .contact {
    position: absolute; top: 440px; width: 360px;
    text-align: center;
  }
  .contact--owen { left: 67px; }
  .contact--daniel { left: 558px; }
  .contact-name {
    font-family: "Bodoni Moda", "Didot", serif;
    font-weight: 500; font-size: 40px; line-height: 1.2;
    -webkit-background-clip: text; background-clip: text; color: transparent;
  }
  .contact-phone {
    font-family: "Open Sans", Arial, sans-serif;
    font-size: 29px; line-height: 1.4; margin-top: 2px;
    -webkit-background-clip: text; background-clip: text; color: transparent;
  }
  .contact--owen .contact-name,
  .contact--owen .contact-phone {
    background-image: linear-gradient(100deg, var(--rose-1), var(--rose-2) 45%, var(--rose-3));
  }
  .contact--daniel .contact-name,
  .contact--daniel .contact-phone {
    background-image: linear-gradient(100deg, var(--gold-1), var(--gold-2) 45%, var(--gold-3));
  }
  .divider {
    position: absolute; left: 485px; top: 413px;
    width: 2px; height: 138px;
    background: linear-gradient(var(--rose-1), var(--rose-3));
  }
</style>
</head>
<body>
  <div class="card">
    <svg class="card-waves" viewBox="0 0 1000 598" aria-hidden="true">
      <defs>
        <linearGradient id="nightFill" x1="0" y1="0" x2="1" y2="1">
          <stop offset="0" stop-color="var(--night-soft)"/>
          <stop offset="0.55" stop-color="var(--night)"/>
          <stop offset="1" stop-color="var(--night-soft)"/>
        </linearGradient>
        <linearGradient id="leafFill" x1="0" y1="0" x2="1" y2="0">
          <stop offset="0" stop-color="var(--leaf)"/>
          <stop offset="0.35" stop-color="var(--leaf-light)"/>
          <stop offset="1" stop-color="var(--leaf)"/>
        </linearGradient>
      </defs>
      <path class="wave-leaf" fill="url(#leafFill)"
        d="M0,299 C200,330 380,370 520,342 C680,300 760,252 880,262 C940,270 980,318 1000,346 L1000,362 C940,300 880,272 800,286 C640,312 560,416 380,410 C220,404 100,384 0,366 Z"/>
      <path class="wave-cream" fill="var(--cream)"
        d="M0,366 C100,384 220,404 380,410 C560,416 640,312 800,286 C880,272 940,300 1000,362 L1000,372 C950,318 880,288 800,298 C650,320 560,428 400,426 C260,424 150,406 0,378 Z"/>
      <path class="wave-night" fill="url(#nightFill)"
        d="M0,378 C150,406 260,424 400,426 C560,428 650,320 800,298 C880,288 950,318 1000,372 L1000,598 L0,598 Z"/>
    </svg>

    <h1 class="company-name">Bramblewood Yardworks</h1>

    <div class="contact contact--owen">
      <p class="contact-name">Owen Platt</p>
      <p class="contact-phone">555-273-9104</p>
    </div>
    <div class="divider"></div>
    <div class="contact contact--daniel">
      <p class="contact-name">Daniel Korbin</p>
      <p class="contact-phone">555-618-3927</p>
    </div>
  </div>
</body>
</html>
```